Telecommunications/Power civil contractor needs business card design

Were a new telecommunications/power underground civil contractor that is looking for a new business card design. Our company colours are silver or grey and orange. Feel free to use the white background logo or the black background logo.

Target Market(s)

Local contractors, utility companies, private sector mining/energy companies, developers.

Industry/Entity Type

Telecommunications

Contact Information for Business Card

Each card will need the following info:
Persons name:
Title:
E-mail:
Phone number:
Shop Address:
Mailing Address:

Requirements
Must have
• Each card will need the following info:
• Persons name:
• Title:
• E-mail:
• Phone number:
• Shop Address:
• Mailing Address:

```html
<!DOCTYPE html>
<html lang="en">
<head>
<meta charset="utf-8">
<title>Grid Line Civil Inc — Business Card</title>
<link rel="stylesheet" href="https://fonts.googleapis.com/css2?family=Arimo:wght@400;700&display=swap">
<style>
  :root {
    --orange: #ee5a24;
    --orange-deep: #d9481a;
    --grey: #6b6b6b;
    --grey-dark: #4a4a4a;
    --rule: #8c8c8c;
    --white: #ffffff;
    --backdrop: #e6e6e6;
  }
  * { margin: 0; padding: 0; box-sizing: border-box; }
  html, body {
    width: 1200px; height: 950px; overflow: hidden;
    background: var(--backdrop);
    font-family: "Arimo", Arial, sans-serif;
  }
  .sheet {
    position: relative; width: 1200px; height: 950px;
    display: flex; flex-direction: column; align-items: center; justify-content: center; gap: 50px;
  }
  .card {
    position: relative; width: 700px; height: 400px;
    box-shadow: 0 6px 18px rgba(0,0,0,.18);
    overflow: hidden;
  }
  /* Back side */
  .card--back {
    background: linear-gradient(135deg, var(--orange) 0%, var(--orange-deep) 100%);
    display: flex; flex-direction: column; align-items: center; justify-content: center; gap: 18px;
  }
  .brand-mark {
    width: 96px; height: 96px; border-radius: 50%;
    border: 5px solid currentColor;
  }
  .card--back .brand-mark { color: var(--white); }
  .card--back .brand-name {
    color: var(--white); font-weight: 700; font-size: 40px; letter-spacing: 1px; text-align: center; line-height: 1.05;
  }
  /* Front side */
  .card--front { background: var(--white); }
  .card--front::after {
    content: ""; position: absolute; left: 0; right: 0; bottom: 0; height: 12px; background: var(--orange);
  }
  .person { position: absolute; left: 44px; top: 70px; }
  .person__name { color: var(--orange); font-size: 28px; font-weight: 700; }
  .person__title { color: var(--grey); font-size: 19px; margin-top: 4px; }
  .contact { position: absolute; left: 44px; top: 170px; list-style: none; }
  .contact li {
    display: flex; align-items: center; gap: 14px;
    color: var(--grey-dark); font-size: 19px; line-height: 30px;
  }
  .contact svg { width: 16px; height: 16px; fill: var(--orange); flex: none; }
  .divider {
    position: absolute; left: 44px; right: 44px; top: 262px;
    height: 1px; background: var(--rule);
  }
  .brand {
    position: absolute; right: 44px; top: 72px;
    display: flex; flex-direction: column; align-items: center; gap: 12px;
  }
  .brand .brand-mark { width: 78px; height: 78px; color: var(--orange); border-width: 4px; }
  .brand .brand-name { color: var(--grey); font-weight: 700; font-size: 30px; text-align: center; line-height: 1.05; }
  .address {
    position: absolute; right: 44px; top: 285px;
    font-style: normal; color: var(--grey-dark); font-size: 20px; line-height: 30px; text-align: left;
  }
</style>
</head>
<body>
<main class="sheet">
  <section class="card card--back" aria-label="Card back">
    <span class="brand-mark" aria-hidden="true"></span>
    <p class="brand-name">GRID LINE<br>CIVIL INC</p>
  </section>

  <section class="card card--front" aria-label="Card front">
    <div class="person">
      <p class="person__name">Marcus Hale</p>
      <p class="person__title">President</p>
    </div>
    <ul class="contact">
      <li>
        <svg viewBox="0 0 16 16" aria-hidden="true"><path d="M3.6 1.2l2.3 2.6-1.2 1.8c.9 2 2.4 3.5 4.4 4.4l1.8-1.2 2.6 2.3-1.4 2.4C6.7 13.4 2.6 9.3 1.2 4z"/></svg>
        555 0142 7788
      </li>
      <li>
        <svg viewBox="0 0 16 16" aria-hidden="true"><path d="M1 3h14v10H1z M1 3l7 5 7-5" fill="var(--orange)"/><path d="M1.5 3.5L8 8.2l6.5-4.7" fill="none" stroke="#fff" stroke-width="1.3"/></svg>
        marcus@example.com
      </li>
      <li>
        <svg viewBox="0 0 16 16" aria-hidden="true"><circle cx="8" cy="8" r="7"/><path d="M1 8h14M8 1c-3 3.5-3 10.5 0 14M8 1c3 3.5 3 10.5 0 14" fill="none" stroke="#fff" stroke-width="1.1"/></svg>
        www.example.com
      </li>
    </ul>
    <div class="brand">
      <span class="brand-mark" aria-hidden="true"></span>
      <p class="brand-name">GRID LINE<br>CIVIL INC</p>
    </div>
    <div class="divider"></div>
    <address class="address">1207 Larkspur Avenue<br>Cedar Falls, NY 10990</address>
  </section>
</main>
</body>
</html>
```